Larkhollow needs a Webpage Design

We need a webpage for Dr. XYZ who is doing consultancy practice in the area of speech, language, and reading disabilities. He is doing his consultancy practice as "Larkhollow Consultants". Our target market is clients with annual income of $100,000 or more in Chicago area. Our business philosophy is: "...We provide the best evidence-based services/interventions, at an affordable fee, and deal only with clients who seek such services...."

Dr. XYZ's area of research interests are: a) using assistive technology for communication for children with autism, b) early intervention with focus on parent participation, and c) language learning for children birth-to-five years.

He works at a public university whose school color is 'Orange". Home page should show two logos (university and practice). Each page should stand on its own and reflect the content with minimal scrolling. The colors should be subdued (not bright colors) to attract college educated wealthy individuals who are seeking best evidence-based practice in speech, language, and reading for their children.

We need five pages: Home, Consultation, Research, Professional Development, and Contact (with google map directions). The home page should have space for a picture and links for facebook, twitter, and google plus. Other pages should have space for at least one picture and links to pdf files.

The overall design should show healthcare service, evidence-based early intervention with focus on parent participation, and project that we are leaders in the field.

```html
<!DOCTYPE html>
<html lang="en">
<head>
<meta charset="utf-8">
<title>Larkhollow Consultants</title>
<link href="https://fonts.googleapis.com/css2?family=Open+Sans:wght@400;600;700&display=swap" rel="stylesheet">
<style>
:root{
  --teal-dark:#16726b;
  --teal-nav:#1f9b96;
  --teal-text:#1a7a72;
  --ink:#3a3a3a;
  --body:#555;
  --rule:#d8d8d8;
  --card:#f1f1f1;
  --card-border:#e2e2e2;
  --orange:#f08a1c;
  --orange-dark:#d8740c;
  --footer:#262626;
  --white:#fff;
}
*{box-sizing:border-box;margin:0;padding:0}
html,body{width:1009px;height:1200px;overflow:hidden;background:var(--white)}
body{font-family:"Open Sans",Arial,sans-serif;color:var(--body);position:relative}
.header{position:absolute;left:0;top:0;width:1009px;height:436px;background:var(--teal-dark)}
.brand{position:absolute;left:114px;top:28px;color:var(--white);font-weight:700;font-size:18px;letter-spacing:.3px;text-transform:uppercase}
.phone{position:absolute;left:741px;top:26px;display:flex;align-items:center;gap:8px;color:var(--white);font-size:14px}
.nav{position:absolute;left:109px;top:77px;width:791px;height:39px;background:var(--teal-nav);border-radius:5px 5px 0 0;display:flex}
.nav a{color:var(--white);text-decoration:none;font-size:12px;font-weight:600;text-transform:uppercase;line-height:39px;text-align:center;border-right:1px solid rgba(0,0,0,.15)}
.nav a:last-child{border-right:none}
.hero{position:absolute;left:109px;top:116px;width:791px;height:320px;background:linear-gradient(90deg,#e9e6e0 0%,#d9c3c8 30%,#f1ece6 55%,#3d5fa8 85%,#8cc47a 100%)}
.dots{position:absolute;left:472px;top:413px;display:flex;gap:6px}
.dots span{width:8px;height:8px;border-radius:50%;background:#bbb}
.dots span:first-child{background:var(--teal-dark)}
.section-title{position:absolute;left:113px;font-size:18px;font-weight:400;color:var(--ink)}
.section-title em{font-style:normal;color:var(--teal-text)}
.rule{position:absolute;left:113px;width:787px;border-top:1px dotted var(--rule)}
.welcome-photo{position:absolute;left:109px;top:520px;width:181px;height:116px;border:1px solid #ccc;border-radius:4px;padding:3px;background:var(--white)}
.welcome-photo div{width:100%;height:100%;background:linear-gradient(90deg,#cfd9e4,#eef2e2,#a6c2d6)}
.welcome-text{position:absolute;left:314px;top:526px;width:585px;font-size:11px;line-height:16.8px;text-align:justify}
.cards{position:absolute;left:110px;top:720px;display:flex;gap:29px}
.card{width:243px;height:344px;background:var(--card);border:1px solid var(--card-border);border-radius:3px;padding:20px 12px 0;position:relative}
.card-photo{width:213px;height:86px}
.card h3{font-size:14.5px;line-height:17px;font-weight:600;color:var(--ink);margin:21px 2px 0}
.card p{position:absolute;left:15px;top:180px;width:210px;font-size:10.3px;line-height:15.2px;text-align:justify}
.btn{position:absolute;left:72px;top:300px;width:82px;height:23px;background:linear-gradient(var(--orange),var(--orange-dark));color:var(--white);font-size:11px;text-align:center;line-height:23px;border-radius:2px;text-decoration:none;box-shadow:1px 1px 2px rgba(0,0,0,.25)}
.footer{position:absolute;left:0;top:1108px;width:1009px;height:92px;background:var(--footer);color:var(--white)}
.footer-links{position:absolute;left:112px;top:20px;font-size:11px}
.footer-links a{color:var(--white);text-decoration:none}
.footer-links span{margin:0 9px}
.copyright{position:absolute;left:112px;top:46px;font-size:11px}
.social{position:absolute;left:811px;top:32px;display:flex;gap:9px}
.social span{width:14px;height:14px;border-radius:50%;background:#9a9a9a}
</style>
</head>
<body>
<header class="header">
  <div class="brand">Larkhollow Consultants</div>
  <div class="phone">
    <svg width="22" height="22" viewBox="0 0 22 22" aria-hidden="true"><circle cx="11" cy="11" r="10" fill="none" stroke="#fff" stroke-width="1.5"/><path d="M8 6c-1 .5-1.5 1.5-1 3 .8 2.5 2.6 4.5 5 5.8 1.3.6 2.3.3 3-.6l-1.8-1.6-1.2.8c-1.3-.7-2.3-1.8-3-3.1l.8-1.2z" fill="#fff"/></svg>
    <span>Tel: +1 555 014 2290</span>
  </div>
  <nav class="nav">
    <a href="#" style="width:96px">Home</a>
    <a href="#" style="width:127px">Consultation</a>
    <a href="#" style="width:114px">Research</a>
    <a href="#" style="width:228px">Professional Development</a>
    <a href="#" style="width:115px">Contact</a>
  </nav>
  <div class="hero" role="img" aria-label="Therapist playing finger puppets with a young girl at a table"></div>
  <div class="dots"><span></span><span></span><span></span><span></span></div>
</header>

<h2 class="section-title" style="top:462px">Welcome to&nbsp; <em>Larkhollow Consultants</em></h2>
<div class="rule" style="top:494px"></div>
<div class="welcome-photo"><div role="img" aria-label="Therapist working with a little boy at a play table"></div></div>
<p class="welcome-text">Sed ut perspiciatis unde omnis iste natus error sit volutem accusantium doloremque laudantium, totam rem aperiam, eaque ipsa quae ab illo inventore veritatis. et quasi architecto beatae vitae dicta sunt explicabo. Nemo enim ipsam voluptatem quia voluptas sit aspernatur aut odit aut fugit, sed quia consequuntur magni dolores eos qui ratione voluptatem sequi nesciunt. aperiam, eaque ipsa quae ab illo inventore veritatis. et quasi architecto beatae vitae dicta sunt explicabo. Nemo enim ipsam voluptatem quia voluptas sit aspernatur aut odit aut fugit, sed quia consequuntur magni dolores eos qui ratione voluptatem sequi nesciunt.ipsam voluptatem quia voluptas sit aspernatur aut odit aut fugit.</p>

<h2 class="section-title" style="top:666px">We <em>Research on</em></h2>
<div class="rule" style="top:697px"></div>

<div class="cards">
  <article class="card">
    <div class="card-photo" role="img" aria-label="Boy practising speech with a therapist" style="background:linear-gradient(90deg,#4a3327,#a57b5a,#8fae6a)"></div>
    <h3>Using assistive technology for communication for children with autism,</h3>
    <p>Sed ut perspiciatis unde omnis iste natus error sit volutem accusantium doloremque laudantium, totam rem aperiam, eaque ipsa quae ab illo inventore veritatis. et quasi architecto beatae vitae dicta sunt explicabo. Nemo enim ipsam voluptatem quia voluptas</p>
    <a class="btn" href="#">Read more</a>
  </article>
  <article class="card">
    <div class="card-photo" role="img" aria-label="Parent playing with two toddlers and toys" style="background:linear-gradient(90deg,#c9a978,#9e3a2e,#d6b98a,#c8a35a)"></div>
    <h3>Early intervention with focus on parent participation</h3>
    <p>Sed ut perspiciatis unde omnis iste natus error sit volutem accusantium doloremque laudantium, totam rem aperiam, eaque ipsa quae ab illo inventore veritatis. et quasi architecto beatae vitae dicta sunt explicabo. Nemo enim ipsam voluptatem quia voluptas</p>
    <a class="btn" href="#">Read more</a>
  </article>
  <article class="card">
    <div class="card-photo" role="img" aria-label="Child and teacher with a learning game" style="background:linear-gradient(90deg,#6a5a4c,#d8d7cf,#3a5bb0,#d7dc9a)"></div>
    <h3>Language learning for children birth-to-five years.</h3>
    <p>Sed ut perspiciatis unde omnis iste natus error sit volutem accusantium doloremque laudantium, totam rem aperiam, eaque ipsa quae ab illo inventore veritatis. et quasi architecto beatae vitae dicta sunt explicabo. Nemo enim ipsam voluptatem quia voluptas</p>
    <a class="btn" href="#">Read more</a>
  </article>
</div>

<footer class="footer">
  <div class="footer-links"><a href="#">Home</a><span>|</span><a href="#">Consultation</a><span>|</span><a href="#">Research</a><span>|</span><a href="#">Professional Development</a><span>|</span><a href="#">Contact</a></div>
  <div class="copyright">Copyright ©&nbsp; Larkhollow Consultants. All Right Reserved.</div>
  <div class="social"><span aria-label="Social link 1"></span><span aria-label="Social link 2"></span><span aria-label="Social link 3"></span></div>
</footer>
</body>
</html>
```